Verodex business card

Business card for sustainable investment company called "Verodex". Verodex is an exchange platform selling carbon credits between buyers and sellers. Carbon Credits are an environmental commodity for reducing global carbon emissions.

the card should obviously have our logo and the theme should be sustainability/environment mixed with a trading platform.

Contact Information for Business Card

Logo, Name, Title, Phone, Email

Colors
0054AA
0677BA
7BADD7
CADEEF
E8F1F8
0094D4
00A9DD
6FCCEA
C7EBF8
E9F6FB
00AB8E
00BBA5
67D7C9
C6EFE9
E9F9F6
59FF00
82FF00
B8FF75
E3FFCB
F4FFEA

```html
<!DOCTYPE html>
<html lang="en">
<head>
<meta charset="utf-8">
<title>Verodex business card</title>
<link rel="stylesheet" href="https://fonts.googleapis.com/css2?family=Montserrat:wght@500;700&family=Poppins:wght@400&display=swap">
<style>
  :root {
    --page-bg: #1a1a1a;
    --card-bg: #101010;
    --card-edge: #1c1c1c;
    --brand-blue: #2b8fe6;
    --steel: #344d6b;
    --steel-soft: #3e5876;
    --accent-line: #00a9dd;
  }
  * { box-sizing: border-box; margin: 0; padding: 0; }
  html, body {
    width: 1200px; height: 900px; overflow: hidden;
    background: var(--page-bg);
  }
  .canvas {
    position: relative; width: 1200px; height: 900px;
    display: flex; flex-direction: column; align-items: center; justify-content: center; gap: 50px;
  }
  .card {
    width: 620px; height: 354px;
    background: var(--card-bg);
    border: 1px solid var(--card-edge);
    box-shadow: 0 14px 30px rgba(0,0,0,.55);
    display: flex; flex-direction: column; align-items: center; justify-content: center;
  }
  .wordmark {
    display: flex; align-items: center; gap: 14px;
    font-family: "Montserrat", sans-serif; font-weight: 700;
    color: var(--brand-blue); letter-spacing: 3px; text-transform: uppercase;
  }
  .wordmark-square { display: block; background: var(--brand-blue); }
  .card-front .wordmark { font-size: 44px; }
  .card-front .wordmark-square { width: 34px; height: 34px; }
  .card-back .wordmark { font-size: 34px; margin-bottom: 22px; }
  .card-back .wordmark-square { width: 28px; height: 28px; }
  .person-name {
    font-family: "Montserrat", sans-serif; font-weight: 700;
    font-size: 24px; letter-spacing: 1px; text-transform: uppercase;
    color: var(--steel);
  }
  .person-title {
    font-family: "Poppins", sans-serif; font-size: 17px;
    color: var(--steel-soft); margin-top: 2px; letter-spacing: .5px;
  }
  .divider { width: 56px; height: 1px; background: var(--accent-line); margin: 16px 0 12px; }
  .contact-list { list-style: none; text-align: center; }
  .contact-list li {
    font-family: "Poppins", sans-serif; font-size: 17px; line-height: 1.35;
    color: var(--steel-soft); letter-spacing: .5px;
  }
</style>
</head>
<body>
  <main class="canvas">
    <section class="card card-front">
      <div class="wordmark"><span class="wordmark-square"></span>Verodex</div>
    </section>
    <section class="card card-back">
      <div class="wordmark"><span class="wordmark-square"></span>Verodex</div>
      <p class="person-name">Daniel Hart</p>
      <p class="person-title">Managing Director</p>
      <span class="divider"></span>
      <ul class="contact-list">
        <li>044-987 654 321</li>
        <li>hello@verodex.net</li>
        <li>www.verodex.net</li>
      </ul>
    </section>
  </main>
</body>
</html>
```